Flag Order

We were just looking to order some branding flags to put on our rental equipment for our business. We would like different examples of the colors, shapes, sizes, backgrounds etc. Was thinking of just doing the plains icon instead of the whole logo on there. but open to ideas. preferably not a white background as they could get dirty,

```html
<!DOCTYPE html>
<html lang="en">
<head>
<meta charset="utf-8">
<title>Ridgeway Rentals – Feather Flag Guide</title>
<link href="https://fonts.googleapis.com/css2?family=Montserrat:wght@400;500;800&display=swap" rel="stylesheet">
<style>
  :root {
    --red: #E20400;
    --blue: #197BCE;
    --yellow: #FFE400;
    --ink: #161616;
    --white: #FFFFFF;
    --paper: #FFFFFF;
    --rule: #555555;
  }
  * { margin: 0; padding: 0; box-sizing: border-box; }
  html, body { width: 857px; height: 1200px; overflow: hidden; background: var(--paper); }
  body { font-family: "Montserrat", sans-serif; color: var(--ink); position: relative; }
  .flag-row { position: absolute; left: 0; top: 0; width: 857px; height: 570px; }
  .section-title {
    position: absolute; left: 0; width: 857px; text-align: center;
    font-weight: 500; font-size: 21px; letter-spacing: 3px;
  }
  .color-guide-title { top: 608px; }
  .swatches { position: absolute; top: 652px; left: 0; width: 857px; height: 50px; }
  .swatch { position: absolute; width: 100px; margin-left: -50px; text-align: center; }
  .swatch-dot {
    width: 26px; height: 26px; border-radius: 50%; margin: 0 auto 4px;
  }
  .swatch-dot.is-white { border: 1px solid #e6e6e6; }
  .swatch-code { font-size: 13.5px; letter-spacing: 1.5px; font-weight: 400; }
  .size-guide-title { top: 752px; }
  .size-note {
    position: absolute; top: 793px; left: 0; width: 857px; text-align: center;
    font-size: 11.5px;
  }
  .size-diagram { position: absolute; left: 0; top: 820px; width: 857px; height: 250px; }
  .dim-label { font-family: "Montserrat", sans-serif; font-size: 12.5px; letter-spacing: 1px; fill: var(--ink); }
</style>
</head>
<body>

  <svg class="flag-row" viewBox="0 0 857 570" aria-label="Four feather flag colourways">
    <defs>
      <path id="feather" d="M0,404 L0,135 C0,58 42,12 107,0 L107,404 Z"/>
    </defs>

    <!-- black colourway -->
    <g transform="translate(76,62)">
      <line x1="1" y1="404" x2="1" y2="486" stroke="var(--ink)" stroke-width="3"/>
      <rect x="-30" y="486" width="60" height="6" fill="var(--ink)"/>
      <use href="#feather" fill="var(--ink)"/>
      <text transform="translate(62,212) rotate(90)" text-anchor="middle" font-family="Montserrat, sans-serif" font-weight="800" font-size="27" fill="var(--white)">RIDGEWAY RENTALS</text>
    </g>

    <!-- blue colourway -->
    <g transform="translate(278,62)">
      <line x1="1" y1="404" x2="1" y2="486" stroke="var(--ink)" stroke-width="3"/>
      <rect x="-30" y="486" width="60" height="6" fill="var(--ink)"/>
      <use href="#feather" fill="var(--blue)"/>
      <text transform="translate(62,212) rotate(90)" text-anchor="middle" font-family="Montserrat, sans-serif" font-weight="800" font-size="27" fill="var(--white)">RIDGEWAY RENTALS</text>
    </g>

    <!-- red colourway -->
    <g transform="translate(472,62)">
      <line x1="1" y1="404" x2="1" y2="486" stroke="var(--ink)" stroke-width="3"/>
      <rect x="-30" y="486" width="60" height="6" fill="var(--ink)"/>
      <use href="#feather" fill="var(--red)"/>
      <text transform="translate(62,222) rotate(90)" text-anchor="middle" font-family="Montserrat, sans-serif" font-weight="800" font-size="27" fill="var(--white)">RIDGEWAY RENTALS</text>
    </g>

    <!-- yellow colourway -->
    <g transform="translate(666,62)">
      <line x1="1" y1="404" x2="1" y2="486" stroke="var(--ink)" stroke-width="3"/>
      <rect x="-30" y="486" width="60" height="6" fill="var(--ink)"/>
      <use href="#feather" fill="var(--yellow)"/>
      <text transform="translate(62,212) rotate(90)" text-anchor="middle" font-family="Montserrat, sans-serif" font-weight="800" font-size="27" fill="var(--ink)">RIDGEWAY RENTALS</text>
    </g>
  </svg>

  <h2 class="section-title color-guide-title">COLOR GUIDE</h2>
  <div class="swatches">
    <div class="swatch" style="left:197px"><div class="swatch-dot" style="background:var(--red)"></div><div class="swatch-code">#E20400</div></div>
    <div class="swatch" style="left:309px"><div class="swatch-dot" style="background:var(--blue)"></div><div class="swatch-code">#197BCE</div></div>
    <div class="swatch" style="left:421px"><div class="swatch-dot" style="background:var(--yellow)"></div><div class="swatch-code">#FFE400</div></div>
    <div class="swatch" style="left:533px"><div class="swatch-dot" style="background:var(--ink)"></div><div class="swatch-code">#161616</div></div>
    <div class="swatch" style="left:644px"><div class="swatch-dot is-white" style="background:var(--white)"></div><div class="swatch-code">#FFFFFF</div></div>
  </div>

  <h2 class="section-title size-guide-title">SIZE GUIDE</h2>
  <p class="size-note">The size can be scaled according to the desired size, referring to the original size.</p>

  <svg class="size-diagram" viewBox="0 820 857 250" aria-label="Flag dimensions 215 by 55 centimetres">
    <text class="dim-label" x="434" y="842" text-anchor="middle">215 Cm</text>
    <g fill="none" stroke="var(--rule)" stroke-width="0.8" stroke-dasharray="4 3">
      <line x1="434" y1="847" x2="434" y2="866"/>
      <line x1="137" y1="866" x2="735" y2="866"/>
      <line x1="137" y1="866" x2="137" y2="880"/>
      <line x1="735" y1="866" x2="735" y2="880"/>
      <line x1="118" y1="888" x2="118" y2="1049"/>
      <line x1="118" y1="888" x2="126" y2="888"/>
      <line x1="118" y1="1049" x2="126" y2="1049"/>
      <line x1="112" y1="967" x2="118" y2="967"/>
    </g>
    <text class="dim-label" x="69" y="971">55 Cm</text>

    <path d="M137,888 L735,888 L735,1049 L295,1049 C205,1049 137,980 137,888 Z" fill="var(--ink)"/>
    <text x="470" y="975" text-anchor="middle" font-family="Montserrat, sans-serif" font-weight="800" font-size="34" fill="var(--white)">RIDGEWAY RENTALS</text>
  </svg>

</body>
</html>
```